Veltrane Group Business Card Design

The CEO is looking for a new trendy look for his business card.
You can stay with current branding or come up with something new/creative. It can be 3D, including Medical Office buildings. You can use our logo in a variety of colors. Please include name, title, company name, company website, email address, cell number

Target Market(s)

Real Estate Development and Construction

Industry/Entity Type

Health care real estate

Contact Information for Business Card

Rohesh Kamdar, CEO M-604.781.2249 E-roheshkamdar@veltrane.com Address:4180 Lindqvist Ave, Tampa, FL 33482 www.veltrane.com

Font styles to use
Other font styles liked:
• Be creative

Requirements
Must have
• Creative, trendy look
Nice to have
• Please go to our website to get a feel- www. veltrane.com
Should not have
• small fonts

```html
<!DOCTYPE html>
<html lang="en">
<head>
<meta charset="utf-8">
<title>Veltrane Group Business Card</title>
<link rel="stylesheet" href="https://fonts.googleapis.com/css2?family=Arimo:wght@400;700&display=swap">
<style>
  :root {
    --stage-dark: #1c1c1d;
    --stage-mid: #3a3a3c;
    --red-deep: #8c181c;
    --red-bright: #c2262c;
    --card-paper: #ececec;
    --navy: #1f3354;
    --ink: #1b1b1b;
    --rule: #8a8a8a;
    --band-grey: #7c7c7c;
    --white: #ffffff;
  }
  * { margin: 0; padding: 0; box-sizing: border-box; }
  html, body { width: 1200px; height: 1000px; overflow: hidden; }
  body {
    position: relative;
    font-family: "Arimo", Arial, sans-serif;
    background: radial-gradient(ellipse at 50% 30%, var(--stage-mid) 0%, var(--stage-dark) 75%);
  }
  .card {
    position: absolute;
    left: 214px;
    width: 772px;
    height: 440px;
    border-radius: 28px;
    overflow: hidden;
  }
  .card-front {
    top: 36px;
    background: linear-gradient(135deg, var(--red-deep) 0%, var(--red-bright) 30%, var(--red-deep) 50%, var(--red-bright) 72%, var(--red-deep) 100%);
  }
  .front-wordmark {
    position: absolute;
    left: 0; right: 0; top: 180px;
    text-align: center;
    color: var(--white);
    font-weight: 700;
    font-size: 66px;
    letter-spacing: -1px;
  }
  .card-back {
    top: 503px;
    background: var(--card-paper);
  }
  .back-wordmark {
    position: absolute;
    left: 28px; top: 30px;
    color: var(--red-bright);
    font-weight: 700;
    font-size: 36px;
    letter-spacing: -0.5px;
  }
  .holder {
    position: absolute;
    right: 30px; top: 196px;
    text-align: right;
  }
  .holder-name {
    color: var(--red-bright);
    font-weight: 700;
    font-size: 32px;
    letter-spacing: 0.5px;
    line-height: 1;
  }
  .holder-title {
    color: var(--navy);
    font-size: 19px;
    margin-top: 6px;
    letter-spacing: 0.5px;
  }
  .divider {
    position: absolute;
    left: 29px; right: 30px; top: 268px;
    height: 2px;
    background: var(--rule);
  }
  .contact-list {
    position: absolute;
    left: 29px; top: 282px;
    list-style: none;
  }
  .contact-list li {
    display: flex;
    align-items: center;
    gap: 11px;
    height: 30px;
    font-size: 20px;
    color: var(--ink);
  }
  .contact-list svg { width: 20px; height: 22px; }
  .office {
    position: absolute;
    right: 30px; top: 280px;
    text-align: right;
  }
  .office-name {
    color: var(--navy);
    font-size: 27px;
    line-height: 1.1;
  }
  .office-address {
    font-size: 16px;
    color: var(--ink);
    margin-top: 10px;
    line-height: 21px;
  }
  .footer-bands {
    position: absolute;
    left: 0; bottom: 0;
    width: 772px; height: 48px;
  }
  .site-url {
    position: absolute;
    right: 54px; bottom: 13px;
    color: var(--white);
    font-size: 17px;
    letter-spacing: 1.5px;
  }
</style>
</head>
<body>
  <section class="card card-front">
    <div class="front-wordmark">Veltrane Group</div>
  </section>

  <section class="card card-back">
    <div class="back-wordmark">Veltrane Group</div>

    <div class="holder">
      <div class="holder-name">ROHESH KAMDAR</div>
      <div class="holder-title">CEO</div>
    </div>

    <div class="divider"></div>

    <ul class="contact-list">
      <li>
        <svg viewBox="0 0 20 22" aria-hidden="true">
          <rect x="4" y="1" width="12" height="20" rx="2" fill="none" stroke="#1f3354" stroke-width="1.6"/>
          <line x1="8" y1="17.5" x2="12" y2="17.5" stroke="#1f3354" stroke-width="1.6"/>
        </svg>
        <span>M-604.781.2249</span>
      </li>
      <li>
        <svg viewBox="0 0 20 22" aria-hidden="true">
          <path d="M1 11 L19 3 L14 19 L10 13 Z" fill="#1f3354"/>
          <path d="M10 13 L19 3" stroke="#ececec" stroke-width="1.2"/>
        </svg>
        <span>roheshkamdar@veltrane.com</span>
      </li>
    </ul>

    <div class="office">
      <div class="office-name">Veltrane Group</div>
      <div class="office-address">4180 Lindqvist Ave, Tampa,<br>FL 33482</div>
    </div>

    <svg class="footer-bands" viewBox="0 0 772 48" aria-hidden="true">
      <polygon points="0,21 454,21 440,48 0,48" fill="#7c7c7c"/>
      <polygon points="482,0 772,0 772,48 451,48" fill="#1f3354"/>
    </svg>
    <div class="site-url">WWW.VELTRANE.COM</div>
  </section>
</body>
</html>
```